SkyvornQ Business Cards and Stationary Design

Need a design for our business cards and stationary. I want to carry on the theme of the logo. I want the business cards to have a design on the back. I would like the business cards and the stationary to carry the same theme, design scheme, and branding

Target Market(s)

Airlines and Maintenance Facilities

Industry/Entity Type

Aviation

Contact Information for Business Card

Name
Position Title
Address: 4827 Trellis Hollow Road, Fort Pierce, Florida, 34951
Office Number
Mobile Number
Email
Website

Font styles to use
Serif
Sans Serif

Colors

Designer to choose colors to be used in the design.

```html
<!DOCTYPE html>
<html lang="en">
<head>
<meta charset="utf-8">
<title>SkyvornQ Business Card</title>
<link rel="stylesheet" href="https://fonts.googleapis.com/css2?family=Roboto+Condensed:wght@300;700&family=Source+Sans+3:wght@400;700&display=swap">
<style>
  :root{
    --stage:#dcdddf;
    --stage-light:#eeeff0;
    --card:#ffffff;
    --navy:#1d2f5e;
    --navy-deep:#16284c;
    --sky:#2a9fdb;
    --text:#2b2b2b;
    --rule:#b9b9b9;
  }
  *{margin:0;padding:0;box-sizing:border-box}
  html,body{width:1200px;height:1100px;overflow:hidden}
  body{
    background:radial-gradient(ellipse at 50% 40%,var(--stage-light),var(--stage));
    font-family:"Source Sans 3",Arial,sans-serif;
    position:relative;
  }
  .card{
    position:absolute;
    width:784px;height:448px;
    background:var(--card);
    border:1px solid #555;
    border-radius:34px;
    overflow:hidden;
  }
  .card--front{left:72px;top:76px}
  .card--back{left:340px;top:578px}

  .accent-band{
    position:absolute;left:0;right:0;bottom:0;height:86px;
    background:linear-gradient(90deg,var(--navy-deep) 0%,var(--navy) 35%,var(--sky) 75%,var(--navy) 100%);
  }

  .brand{position:absolute;text-align:center;transform:translateX(-50%)}
  .brand-mark{
    display:block;margin:0 auto;border-radius:50%;
    border-style:solid;border-color:var(--navy);
  }
  .brand-name{
    display:block;color:var(--navy);font-weight:700;
    letter-spacing:.14em;white-space:nowrap;
  }
  .card--front .brand{left:224px;top:116px}
  .card--front .brand-mark{width:108px;height:108px;border-width:9px}
  .card--front .brand-name{font-size:36px;margin-top:20px}

  .divider{position:absolute;left:422px;top:76px;width:2px;height:250px;background:var(--rule)}

  .person{position:absolute;left:462px;top:68px}
  .person-name{
    font-family:"Roboto Condensed","Arial Narrow",sans-serif;
    font-weight:700;font-size:29px;color:var(--navy);letter-spacing:.02em;
  }
  .person-title{
    font-family:"Roboto Condensed","Arial Narrow",sans-serif;
    font-weight:300;font-size:24px;color:var(--text);margin-top:-2px;
  }
  .contact{list-style:none;position:absolute;left:462px;top:155px;font-size:17px;color:var(--text)}
  .contact li{display:flex;align-items:flex-start;gap:6px;height:27px;line-height:22px}
  .contact li.address{margin-top:10px;line-height:26px;height:auto;max-width:300px}
  .contact svg{flex:none;margin-top:3px}

  .card--back .back-mark{
    position:absolute;left:57px;top:10px;width:334px;height:334px;
    border-radius:50%;border:18px solid var(--navy);
  }
  .card--back .brand{left:591px;top:172px}
  .card--back .brand-name{font-size:38px}
  .site{display:block;margin-top:8px;font-size:18px;color:var(--text);letter-spacing:.2em}
</style>
</head>
<body>

<section class="card card--front">
  <div class="accent-band" role="img" aria-label="Decorative navy and sky-blue wave band along the lower edge of the card"></div>

  <div class="brand">
    <span class="brand-mark"></span>
    <span class="brand-name">SKYVORNQ</span>
  </div>

  <div class="divider"></div>

  <div class="person">
    <h1 class="person-name">DARREL VANTHORPE</h1>
    <p class="person-title">PRESIDENT</p>
  </div>

  <ul class="contact">
    <li><svg width="16" height="16" viewBox="0 0 16 16"><circle cx="8" cy="8" r="7" fill="none" stroke="#1d2f5e" stroke-width="1.3"/><path d="M5.2,4.5 l1.3,-.4 .8,1.8 -.8,.7 q.6,1.4 1.9,2 l.7,-.8 1.8,.8 -.4,1.3 q-3.2,.3 -5.3,-5.4z" fill="#1d2f5e"/></svg>012-345-6789</li>
    <li><svg width="16" height="16" viewBox="0 0 16 16"><circle cx="8" cy="8" r="7" fill="none" stroke="#1d2f5e" stroke-width="1.3"/><rect x="5.5" y="4" width="5" height="8" rx="1" fill="none" stroke="#1d2f5e" stroke-width="1.2"/></svg>012-345-6789</li>
    <li><svg width="16" height="16" viewBox="0 0 16 16"><circle cx="8" cy="8" r="7" fill="none" stroke="#1d2f5e" stroke-width="1.3"/><rect x="4.3" y="5.3" width="7.4" height="5.4" fill="none" stroke="#1d2f5e" stroke-width="1.1"/><path d="M4.3,5.3 L8,8.3 L11.7,5.3" fill="none" stroke="#1d2f5e" stroke-width="1.1"/></svg>info@skyvornq.com</li>
    <li><svg width="16" height="16" viewBox="0 0 16 16" fill="none" stroke="#1d2f5e" stroke-width="1.2"><circle cx="8" cy="8" r="7"/><ellipse cx="8" cy="8" rx="3" ry="7"/><path d="M1,8 H15 M2,4.5 H14 M2,11.5 H14"/></svg>www.skyvornq.com</li>
    <li class="address"><svg width="16" height="16" viewBox="0 0 16 16"><circle cx="8" cy="8" r="7" fill="none" stroke="#1d2f5e" stroke-width="1.3"/><path d="M8,12.5 Q4.8,8.8 4.8,6.8 A3.2,3.2 0 0 1 11.2,6.8 Q11.2,8.8 8,12.5z" fill="#1d2f5e"/><circle cx="8" cy="6.8" r="1.2" fill="#fff"/></svg><span>4827 Trellis Hollow Road, Fort Pierce, Florida, 34951</span></li>
  </ul>
</section>

<section class="card card--back">
  <span class="back-mark"></span>
  <div class="brand">
    <span class="brand-name">SKYVORNQ</span>
    <span class="site">www.skyvornq.com</span>
  </div>
</section>

</body>
</html>
```